SaaS Early tech startup business card design

Unique design for experience ecommerce platform company. the business cards will be used by executive members. conformance with color code is required.

```html
<!DOCTYPE html>
<html lang="en">
<head>
<meta charset="utf-8">
<title>novlyn — Business Card</title>
<link rel="stylesheet" href="https://fonts.googleapis.com/css2?family=Open+Sans:wght@400;600;700&display=swap">
<style>
  :root {
    --bg: #1c1c1c;
    --brand-blue: #16668f;
    --brand-teal: #12bb9c;
    --paper: #ffffff;
    --ink: #1f2a33;
  }
  * { box-sizing: border-box; margin: 0; padding: 0; }
  html, body { width: 1200px; height: 988px; overflow: hidden; }
  body {
    background: var(--bg);
    font-family: "Open Sans", Arial, sans-serif;
    display: flex;
    flex-direction: column;
    align-items: center;
    justify-content: center;
    gap: 56px;
  }
  .card {
    position: relative;
    width: 700px;
    height: 400px;
    border-radius: 22px;
    overflow: hidden;
  }
  .card-front {
    background: var(--brand-blue);
    display: flex;
    align-items: center;
    justify-content: center;
  }
  .wordmark {
    font-weight: 700;
    letter-spacing: -2px;
    line-height: 1;
  }
  .card-front .wordmark { font-size: 150px; color: var(--brand-teal); }

  .card-back { background: var(--paper); }
  .card-back .wordmark {
    position: absolute; left: 56px; top: 70px;
    font-size: 84px; color: var(--brand-teal);
  }
  .side-tab {
    position: absolute; right: 0; top: 118px;
    width: 14px; height: 46px;
    background: var(--brand-blue);
    border-radius: 6px 0 0 6px;
  }
  .identity {
    position: absolute; right: 44px; top: 118px;
    text-align: right;
  }
  .identity .name {
    font-size: 30px; font-weight: 700; color: var(--brand-blue); line-height: 1.1;
  }
  .identity .role {
    font-size: 15px; color: var(--ink); margin-top: 2px;
  }
  .divider {
    position: absolute; left: 150px; right: 34px; top: 200px;
    height: 2px; background: var(--brand-blue);
  }
  .address {
    position: absolute; right: 44px; top: 216px;
    text-align: right; font-size: 16px; color: var(--ink); line-height: 1.45;
  }
  .contact {
    position: absolute; left: 150px; top: 268px;
    list-style: none;
    font-size: 16px; color: var(--ink); line-height: 1.55;
  }
  .contact li { display: flex; align-items: center; gap: 10px; white-space: nowrap; }
  .contact svg { width: 14px; height: 14px; fill: var(--brand-blue); flex: none; }
  .footer-band {
    position: absolute; left: 0; bottom: 0; width: 700px; height: 42px;
  }
</style>
</head>
<body>
  <section class="card card-front" aria-label="Card front">
    <span class="wordmark">novlyn</span>
  </section>

  <section class="card card-back" aria-label="Card back">
    <span class="wordmark">novlyn</span>
    <span class="side-tab"></span>
    <div class="identity">
      <p class="name">Dara Okafor</p>
      <p class="role">Managing Director</p>
    </div>
    <span class="divider"></span>
    <p class="address">Your location street here,<br>Country name, Country - 91542</p>
    <ul class="contact">
      <li>
        <svg viewBox="0 0 16 16" aria-hidden="true"><path d="M3 1l3 3-1.6 2a9 9 0 0 0 5.6 5.6L12 10l3 3-2 2C7 15 1 9 1 3z"/></svg>
        +012 345 6789
      </li>
      <li>
        <svg viewBox="0 0 16 16" aria-hidden="true"><path d="M1 3h14v10H1zM2 4l6 5 6-5v-.5H2z" fill-rule="evenodd"/></svg>
        info@youremail.com
      </li>
      <li>
        <svg viewBox="0 0 16 16" aria-hidden="true"><circle cx="8" cy="8" r="7"/></svg>
        www.yourwebsite.com
      </li>
    </ul>
    <svg class="footer-band" viewBox="0 0 700 42" aria-hidden="true">
      <polygon points="0,0 452,0 446,42 0,42" fill="var(--brand-blue)"/>
      <polygon points="464,0 700,0 700,42 458,42" fill="var(--brand-teal)"/>
    </svg>
  </section>
</body>
</html>
```